we can communicate on this, but i want to follow the approach we took on Pellew|Marsh & Quinlan but i feel the card front needs the black background and the platinum and gold logo. The back? I am open. we can use the same info from PM&Q. Velmont Arc is an enhanced equity investment fund - basically a very exclusive boutique hedge fund that uses only stock options. very advanced things. hope you are interested

Contact Information for Business Card

Dr. Lewis T. Brennick, CFA
Scientifique de fusée financière
701.555.0143
LTBquant47@mailvantor.com

4718 Willow Creek Bend W.
West Fargo, ND 58078

No web site

Colors

Designer to choose colors to be used in the design.

Requirements
Nice to have
• I tend to prefer the most visible applications of the logo to include logo and name, the logo version with a black background and the gold and platinum components separated by the black. I see this working well for a single side (logo and name - this is card front to me).
• I am fairly open to other treatments on the reverse side with the data. To me, it makes sense to have a different color rendition of the logo on the reverse and it may be a muted black tone on tone or an oversized portion that would have spot UV. Or, the reverse may play with colors and layout
Should not have
• Other colors = no no
• Decorative font

```html
<!DOCTYPE html>
<html lang="en">
<head>
<meta charset="utf-8">
<title>Velmont Arc — Business Card</title>
<link rel="stylesheet" href="https://fonts.googleapis.com/css2?family=Lato:wght@400;700&display=swap">
<style>
  :root {
    --backdrop: #5c6063;
    --card-black: #111113;
    --tone-dark: #2b2b2e;
    --tone-grey: #8d8d92;
    --gold: #c9a03c;
    --platinum: #d9d9dc;
    --white: #ffffff;
    --text-grey: #b9b9bd;
  }
  * { box-sizing: border-box; margin: 0; padding: 0; }
  html, body {
    width: 1200px; height: 780px; overflow: hidden;
    background: var(--backdrop);
    font-family: "Lato", Arial, sans-serif;
  }
  .sheet {
    width: 1200px; height: 780px;
    display: flex; flex-direction: column;
    align-items: center; justify-content: center; gap: 24px;
  }
  .card {
    position: relative;
    width: 640px; height: 366px;
    background: var(--card-black);
    box-shadow: 0 6px 18px rgba(0,0,0,.45);
  }

  /* Logo side, tone on tone */
  .card--brand { display: flex; align-items: center; justify-content: center; gap: 22px; }
  .brand-mark {
    width: 110px; height: 110px; border-radius: 50%;
    background: linear-gradient(160deg, #3a3a3d, #1c1c1e);
  }
  .brand-name {
    font-weight: 700; font-size: 44px; letter-spacing: 3px;
    color: var(--tone-grey); text-transform: uppercase;
  }

  /* Contact side */
  .logo-lockup {
    position: absolute; right: 44px; top: 40px;
    display: flex; flex-direction: column; align-items: center; gap: 14px;
  }
  .logo-lockup .mark {
    width: 78px; height: 78px; border-radius: 50%; background: var(--gold);
  }
  .logo-lockup .name {
    font-weight: 700; font-size: 30px; letter-spacing: 2px;
    color: var(--white); text-transform: uppercase;
  }
  .rule {
    position: absolute; left: 40px; right: 40px; top: 214px;
    height: 1px; background: var(--gold);
  }
  .identity { position: absolute; left: 40px; bottom: 162px; }
  .identity .person { color: var(--gold); font-weight: 700; font-size: 25px; }
  .identity .role { color: var(--text-grey); font-size: 15px; margin-top: 4px; }
  .contacts {
    position: absolute; left: 40px; top: 238px;
    list-style: none; display: flex; flex-direction: column; gap: 12px;
  }
  .contacts li {
    display: flex; align-items: center; gap: 14px;
    color: var(--text-grey); font-size: 16px;
  }
  .contacts svg { width: 18px; height: 18px; fill: var(--gold); flex: none; }
  .address {
    position: absolute; right: 40px; top: 238px;
    text-align: right; font-style: normal;
    color: var(--text-grey); font-size: 15px; line-height: 1.6;
  }
</style>
</head>
<body>
<main class="sheet">
  <section class="card card--brand" aria-label="Card logo side">
    <span class="brand-mark"></span>
    <span class="brand-name">Velmont Arc</span>
  </section>

  <section class="card card--contact" aria-label="Card contact side">
    <div class="logo-lockup">
      <span class="mark"></span>
      <span class="name">Velmont Arc</span>
    </div>

    <div class="identity">
      <p class="person">Dr. Lewis T. Brennick, CFA</p>
      <p class="role">Scientifique des Fusées Financières</p>
    </div>

    <div class="rule"></div>

    <ul class="contacts">
      <li>
        <svg viewBox="0 0 24 24" aria-hidden="true"><path d="M6.6 10.8a15.1 15.1 0 0 0 6.6 6.6l2.2-2.2c.3-.3.7-.4 1-.2 1.1.4 2.3.6 3.6.6.6 0 1 .4 1 1V20c0 .6-.4 1-1 1A17 17 0 0 1 3 4c0-.6.4-1 1-1h3.5c.6 0 1 .4 1 1 0 1.3.2 2.5.6 3.6.1.3 0 .7-.2 1z"/></svg>
        <span>701.555.0143</span>
      </li>
      <li>
        <svg viewBox="0 0 24 24" aria-hidden="true"><path d="M2 5h20v14H2zm2 2v.4l8 5.2 8-5.2V7zm0 2.8V17h16V9.8l-8 5.2z"/></svg>
        <span>LTBquant47@mailvantor.com</span>
      </li>
    </ul>

    <address class="address">
      4718 Willow Creek Bend W.<br>
      West Fargo, ND 58078
    </address>
  </section>
</main>
</body>
</html>
```